The Tolvanic Fiber Union Journal (TFUJ) cover page.

We need a unique green font that will be superimposed on all issues of an electronic magazine. It will always have an image in the background referring to one of the articles in each particular number.
The cover of the magazine should read the motto of the Tolvanic Fiber Union: "The JTFU lifts Fiber Study and inspires a Bright Dawn for all."

​

On the back cover, the editor in chief, the editorial committee, the legal notice and the three logos (DRUL, Velibrant, and the society logo) should be mentioned. see power point page.
​
152 / 5.000

On the back cover, the editor in chief, the editorial committee, the legal notice and the three logos (DRUL, Velibrant, ans the society logo) should be mentioned.

Target Market(s)

The journal will be initially aimed at scientists from Latin America and iberoAmerica whose central research topic is plastic materials, eventually it could attract scientists from around the world

Font styles to use
Serif

Colors
59FF00
82FF00
B8FF75
E3FFCB
F4FFEA

Requirements
Must have
• From the beginning in the announcement of the appearance of this new journal, it must capture the attention of the public, the project will be presented at the main annual meeting of the Tolvanic Fiber Union
Nice to have
• in the ppt file I send there is alogo involving two persons exchanging ideas. a variant of this logo will nice to have in the cover page of the journal
Should not have
• the name of current international journals.

```html
<!DOCTYPE html>
<html lang="en">
<head>
<meta charset="utf-8">
<title>Tolvanic Fiber Union Journal — Cover Spread</title>
<link rel="stylesheet" href="https://fonts.googleapis.com/css2?family=Bebas+Neue&family=Poppins:wght@400;500;600;800&display=swap">
<style>
  :root {
    --page-bg: #c6d9de;
    --cover-deep: #121b27;
    --cover-mid: #1d2c3d;
    --teal: #1fa8a6;
    --orange: #e88f48;
    --ink-light: #f1f4f6;
    --ink-soft: #d5dde3;
    --molecule-warm: #b9773a;
    --molecule-cool: #1f5560;
  }
  * { margin: 0; padding: 0; box-sizing: border-box; }
  html, body { width: 858px; height: 1200px; overflow: hidden; background: var(--page-bg); }
  body { position: relative; font-family: "Poppins", sans-serif; color: var(--ink-light); }

  .spread {
    position: absolute; left: 19px; top: 334px; width: 820px; height: 532px;
    background: radial-gradient(ellipse at 70% 45%, var(--cover-mid) 0%, var(--cover-deep) 75%);
    overflow: hidden;
  }
  .panel { position: absolute; top: 0; height: 100%; }
  .back-cover { left: 0; width: 410px; }
  .front-cover { left: 410px; width: 410px; }

  .masthead { position: absolute; text-align: center; line-height: 1; }
  .masthead__lead { font-family: "Bebas Neue", sans-serif; color: var(--teal); display: block; }
  .masthead__society { font-family: "Poppins", sans-serif; font-weight: 800; color: var(--orange); display: block; }
  .masthead__journal { font-family: "Poppins", sans-serif; font-weight: 500; color: var(--ink-light); display: block; }

  .back-cover .masthead { left: 40px; width: 306px; top: 30px; }
  .back-cover .masthead__lead { font-size: 58px; letter-spacing: 0.5px; }
  .back-cover .masthead__society { font-size: 25px; margin-top: -4px; }
  .back-cover .masthead__journal { font-size: 13px; letter-spacing: 6px; margin-top: 2px; }

  .front-cover .masthead { left: 28px; width: 356px; top: 30px; }
  .front-cover .masthead__lead { font-size: 82px; letter-spacing: 0.5px; }
  .front-cover .masthead__society { font-size: 32px; margin-top: -6px; }
  .front-cover .masthead__journal { font-size: 17px; letter-spacing: 7px; margin-top: 1px; }

  .editor { position: absolute; text-align: center; line-height: 1.2; }
  .editor__role { display: block; color: var(--teal); font-weight: 500; letter-spacing: 2px; }
  .editor__name { display: block; color: var(--orange); font-weight: 500; }
  .back-cover .editor { left: 40px; width: 306px; top: 130px; }
  .back-cover .editor__role { font-size: 9.5px; }
  .back-cover .editor__name { font-size: 14px; margin-top: 2px; }
  .front-cover .editor { left: 28px; width: 356px; top: 464px; }
  .front-cover .editor__role { font-size: 10px; }
  .front-cover .editor__name { font-size: 14px; margin-top: 2px; }

  .roster {
    position: absolute; top: 185px; width: 152px; height: 227px;
    border: 1px solid var(--teal); border-radius: 7px; text-align: center; padding-top: 12px;
  }
  .roster--board { left: 25px; }
  .roster--committee { left: 196px; }
  .roster__title { font-size: 11px; font-weight: 600; margin-bottom: 7px; }
  .roster--board .roster__title { color: var(--teal); }
  .roster--committee .roster__title { color: var(--orange); margin-top: 4px; }
  .roster__list { list-style: none; font-size: 6.3px; line-height: 1.3; color: var(--ink-soft); }
  .roster--board .roster__list li { margin-bottom: 6px; }
  .roster--committee .roster__list li { margin-bottom: 6.2px; }

  .partners { position: absolute; top: 458px; left: 25px; display: flex; align-items: center; gap: 10px; }
  .partner { display: flex; align-items: center; gap: 4px; font-family: "Poppins", sans-serif; font-weight: 600; color: var(--ink-light); }
  .partner--drul { flex-direction: column; gap: 2px; }
  .partner--drul .partner__name { font-size: 22px; letter-spacing: 2px; line-height: 1; }
  .partner--drul .partner__sub { font-size: 5px; font-weight: 600; text-align: center; line-height: 1.2; }
  .partner--velibrant .partner__name { font-size: 7px; }
  .partner__dot { width: 14px; height: 14px; border-radius: 50%; background: var(--ink-light); }

  .legal { position: absolute; left: 188px; top: 460px; width: 200px; font-size: 4.3px; line-height: 1.35; color: var(--ink-soft); }

  .cover-art {
    position: absolute; left: 55px; top: 172px; width: 270px; height: 218px; border-radius: 50%;
    background: radial-gradient(circle at 50% 50%, var(--molecule-warm) 0%, var(--molecule-cool) 45%, rgba(29,44,61,0) 72%);
  }
  .motto { position: absolute; left: 28px; width: 356px; top: 418px; text-align: center; font-size: 13px; line-height: 1.3; color: var(--ink-light); }
</style>
</head>
<body>
  <main class="spread">
    <section class="panel back-cover" aria-label="Back cover">
      <h2 class="masthead">
        <span class="masthead__lead">THE TOLVANIC</span>
        <span class="masthead__society">FIBER UNION</span>
        <span class="masthead__journal">JOURNAL(TFUJ)</span>
      </h2>
      <p class="editor">
        <span class="editor__role">EDITOR IN CHIEF</span>
        <span class="editor__name">Dr. Aurelio Brenna-Costa</span>
      </p>

      <div class="roster roster--board">
        <h3 class="roster__title">EDITORIAL BOARD</h3>
        <ul class="roster__list">
          <li>Dr. Teodoro Valmes Ruiz<br>DRUL)</li>
          <li>Dr. Lucio Ferrand<br>(IMVA)</li>
          <li>Dr. Ismael Corvo<br>(UA del Norte)</li>
          <li>Dr. Óscar Lindaro<br>(ITCosta)</li>
          <li>Dr. Emilio Sastre Vidal.</li>
          <li>Dr. Gabriel Orza Montes<br>(Universidad de Valdora)</li>
          <li>Dr. Emilio Sastre Vidal<br>(universidad de Pradera)</li>
          <li>J. Noemí Areto SALAS<br>(UNIVERSIDAD SERRANA)</li>
        </ul>
      </div>

      <div class="roster roster--committee">
        <h3 class="roster__title">EDITORIAL COMMITEE</h3>
        <ul class="roster__list">
          <li>Dr. Teodoro Valmes Ruiz(DRUL)</li>
          <li>Dr. Lucio Ferrand(IMVA)</li>
          <li>Dr. Ismael Corvo (UA del Norte)</li>
          <li>Dr. Óscar Lindaro Peral</li>
          <li>Dr. Emilio Sastre Vidal</li>
          <li>Dr. Gabriel Orza Montes<br>(Universidad de Valdora)</li>
          <li>Dr. Emilio Sastre Vidal<br>(universidad de Pradera)</li>
          <li>J. Noemí Areto SALAS<br>(UNIVERSIDAD SERRANA)</li>
          <li>Dr. Mauro Quintel Ríos</li>
          <li>Dr. Hugo Belmar</li>
          <li>Dr. Irene Solva Marquina</li>
        </ul>
      </div>

      <div class="partners">
        <div class="partner partner--drul">
          <span class="partner__name">DRUL</span>
          <span class="partner__sub">CENTRO DE ESTUDIOS<br>EN FIBRAS</span>
        </div>
        <div class="partner partner--velibrant">
          <span class="partner__dot"></span>
          <span class="partner__name">Velibrant</span>
        </div>
      </div>

      <p class="legal">TFUJ, vol. 6, núm. 12, septiembre 2023–febrero 2024, es una revista académica digital de acceso libre y publicación cuatrimestral editada por DRUL, Av. Lumen 140, Col. Arbolada, C.P. 00000, Ciudad Veranda. Tel. +00 (000) 000 0000. Contacto: editorial@tfuj.example. Directora de la revista: Dra. Celia Nuar. Responsable de la última actualización: Iván Roca. Fecha de última modificación: 21 de septiembre de 2023.</p>
    </section>

    <section class="panel front-cover" aria-label="Front cover">
      <h1 class="masthead">
        <span class="masthead__lead">THE TOLVANIC</span>
        <span class="masthead__society">FIBER UNION</span>
        <span class="masthead__journal">JOURNAL(TFUJ)</span>
      </h1>
      <div class="cover-art" role="img" aria-label="Illustration of a glossy molecular structure with copper and teal spheres joined by bonds"></div>
      <p class="motto">The JTFU lifts Fiber Study and<br>inspires a Bright Dawn for all.</p>
      <p class="editor">
        <span class="editor__role">EDITOR IN CHIEF</span>
        <span class="editor__name">Dr. Aurelio Brenna-Costa</span>
      </p>
    </section>
  </main>
</body>
</html>
```